Corvin Ridge Software PowerPoint template

We are a software company selling endpoint visibility, access and security technology to enterprise-level IT departments.
Our technology helps organizations gain comprehensive visibility into and control over devices accessing their corporate network so they can quickly identify and address suspicious activity on the network that could lead to potential threats like data breaches.
This technology can cost organizations upwards of $1M - depending on the size of the organization. Our primary clients are Vestral 2,000 companies.
We want a professional, polished PowerPoint template that we can use for all company presentations. Please include:
Title page
Section page
General info page
Thank you page
Logo options and color specs are attached.
Please include our tagline on at least the title page: Discover the edge. Optimize the whole.
Reason: Seeking more options. Looking for a clean design that uses lots of white space.
Software

```html
<!DOCTYPE html>
<html lang="en">
<head>
<meta charset="utf-8">
<title>Corvin Ridge Software – Thank You Slide</title>
<link rel="stylesheet" href="https://fonts.googleapis.com/css2?family=Jost:wght@500;600&family=Questrial&family=Arimo:wght@700&display=swap">
<style>
  :root {
    --slide-red: #8c0308;
    --slide-red-soft: #960d12;
    --accent-orange: #e8884a;
    --footer-orange: #df7b4f;
    --contact-pink: #e6a2a2;
    --white: #ffffff;
  }
  * { margin: 0; padding: 0; box-sizing: border-box; }
  html, body {
    width: 1200px;
    height: 900px;
    overflow: hidden;
    background: var(--slide-red);
  }
  .slide {
    position: relative;
    width: 1200px;
    height: 900px;
    overflow: hidden;
  }
  .slide-backdrop {
    position: absolute;
    inset: 0;
    background: radial-gradient(circle at 50% 45%, var(--slide-red-soft), var(--slide-red) 75%);
  }
  .brand {
    position: absolute;
    left: 60px;
    top: 416px;
    display: flex;
    align-items: center;
    gap: 26px;
  }
  .brand-mark {
    width: 64px;
    height: 64px;
    flex: none;
  }
  .brand-name {
    font-family: "Jost", sans-serif;
    font-weight: 500;
    font-size: 40px;
    line-height: 1.1;
    letter-spacing: 3px;
    color: var(--white);
    text-transform: uppercase;
  }
  .closing {
    position: absolute;
    left: 650px;
    top: 356px;
  }
  .closing-title {
    font-family: "Jost", sans-serif;
    font-weight: 600;
    font-size: 43px;
    letter-spacing: 0.5px;
    color: var(--accent-orange);
    line-height: 1;
    margin-bottom: 22px;
  }
  .contact-list {
    list-style: none;
    margin-left: 3px;
  }
  .contact-list li {
    font-family: "Questrial", sans-serif;
    font-size: 21px;
    line-height: 30px;
    color: var(--contact-pink);
  }
  .footer-band {
    position: absolute;
    left: 0;
    bottom: 0;
    width: 100%;
    height: 42px;
    background: var(--footer-orange);
    display: flex;
    align-items: center;
    justify-content: space-between;
    padding: 0 22px 0 12px;
    font-family: "Arimo", sans-serif;
    font-weight: 700;
    font-size: 16px;
    color: var(--white);
  }
</style>
</head>
<body>
  <main class="slide">
    <div class="slide-backdrop" role="img" aria-label="Repeating pattern of soft translucent circles over the red slide background"></div>

    <div class="brand">
      <svg class="brand-mark" viewBox="0 0 64 64" aria-hidden="true">
        <circle cx="32" cy="32" r="30" fill="var(--white)"/>
      </svg>
      <div class="brand-name">Corvin Ridge<br>Software</div>
    </div>

    <section class="closing">
      <h1 class="closing-title">THANKS FOR YOUR TIME</h1>
      <ul class="contact-list">
        <li>Contact Details here Contact Details here</li>
        <li>Contact Details here Contact Details here</li>
        <li>Contact Details here Contact Details here</li>
        <li>Contact Details here Contact Details here</li>
      </ul>
    </section>

    <footer class="footer-band">
      <span class="footer-copyright">COPYRIGHT TEXT HERE</span>
      <span class="footer-page">Page : 01</span>
    </footer>
  </main>
</body>
</html>
```